Tech business card design

We need an amazing business card design for our new business 'Pexla' a marketing tech startup based in Sydney, Australia. We provide an online marketplace for businesses to search and buy advertising media, connect with service providers and learn more about marketing. We wish to communicate 'cool tech', reliability and professionalism and design based around our logo.

Target Market(s)

Business Owners

Contact Information for Business Card

Name
Position
Email Address
Website
Phone Number

Font styles to use
Other font styles liked:
• Avenir & Avenir Next

Colors

Designer to choose colors to be used in the design.

```html
<!DOCTYPE html>
<html lang="en">
<head>
<meta charset="UTF-8">
<title>Pexla Business Card</title>
<link rel="stylesheet" href="https://fonts.googleapis.com/css2?family=Nunito+Sans:ital,wght@0,400;0,700;0,900;1,700&display=swap">
<style>
  :root {
    --navy: #1b1c4f;
    --navy-deep: #15163f;
    --white: #ffffff;
    --ink: #1b1c4f;
    --rule: #2a2b55;
    --backdrop: #2b2b30;
    --font: "Nunito Sans", Arial, sans-serif;
  }
  * { margin: 0; padding: 0; box-sizing: border-box; }
  html, body { width: 1200px; height: 800px; overflow: hidden; }
  body { background: var(--backdrop); font-family: var(--font); position: relative; }

  .card { position: absolute; border-radius: 6px; overflow: hidden; box-shadow: 0 12px 30px rgba(0,0,0,.45); }

  /* Front */
  .card-front { left: 90px; top: 240px; width: 560px; height: 320px; background: var(--navy); }
  .front-brand { position: absolute; left: 150px; top: 92px; color: var(--white); }
  .brand-name { font-weight: 900; font-size: 96px; letter-spacing: -2px; line-height: 1; }
  .brand-tm { position: absolute; top: 8px; right: -26px; font-size: 13px; font-weight: 700; }
  .front-url { position: absolute; left: 160px; top: 210px; color: var(--white); font-size: 13px; letter-spacing: 6.5px; }

  /* Back */
  .card-back { left: 760px; top: 110px; width: 340px; height: 580px; background: var(--white); color: var(--ink); }
  .back-brand { position: absolute; left: 36px; top: 40px; color: var(--ink); }
  .back-brand .brand-name { font-size: 92px; }
  .back-brand .brand-tm { top: auto; bottom: -14px; right: 4px; font-size: 11px; }

  .contact { position: absolute; left: 0; width: 100%; text-align: center; }
  .person { top: 178px; }
  .person-name { font-weight: 900; font-size: 22px; }
  .person-role { font-size: 17px; margin-top: -3px; }
  .label { font-weight: 700; font-style: italic; font-size: 13px; }
  .value { font-size: 16px; }
  .phone { top: 252px; }
  .email { top: 300px; }
  .address { top: 360px; font-size: 16px; line-height: 1.15; }

  .rule { position: absolute; height: 2px; background: var(--rule); }
  .rule-a { left: 54px; width: 232px; top: 238px; }
  .rule-b { left: 54px; width: 232px; top: 348px; }
  .rule-c { left: 54px; width: 232px; top: 442px; }

  .social { position: absolute; top: 429px; left: 0; width: 100%; display: flex; justify-content: center; gap: 8px; }
  .social-dot { width: 28px; height: 28px; border-radius: 50%; background: var(--white); border: 3px solid var(--navy); box-shadow: 0 0 0 2px var(--white); }

  .back-band { position: absolute; left: 0; bottom: 0; width: 340px; height: 90px; }
  .band-url { position: absolute; left: 0; bottom: 14px; width: 100%; text-align: center; color: var(--white); font-size: 17px; letter-spacing: .5px; }
  .band-url strong { font-weight: 900; }
</style>
</head>
<body>
  <section class="card card-front">
    <div class="front-brand">
      <span class="brand-name">pexla</span><span class="brand-tm">TM</span>
    </div>
    <p class="front-url">www.pexlaweb.com</p>
  </section>

  <section class="card card-back">
    <div class="back-brand">
      <span class="brand-name">pexla</span><span class="brand-tm">TM</span>
    </div>

    <div class="contact person">
      <p class="person-name">Mara Ellison</p>
      <p class="person-role">Manager</p>
    </div>
    <div class="rule rule-a"></div>
    <div class="contact phone">
      <p class="label">Phone:</p>
      <p class="value">02 8123 4400</p>
    </div>
    <div class="contact email">
      <p class="label">Email:</p>
      <p class="value">hello@pexlamail.com</p>
    </div>
    <div class="rule rule-b"></div>
    <div class="contact address">
      <p>PO BOX 48, Kent Road</p>
      <p>3rd street Sydney</p>
      <p>Australia</p>
    </div>
    <div class="rule rule-c"></div>
    <div class="social">
      <span class="social-dot"></span>
      <span class="social-dot"></span>
    </div>

    <svg class="back-band" viewBox="0 0 340 90" aria-hidden="true">
      <path d="M0 0 H40 Q52 0 52 14 V40 Q52 50 64 50 H340 V90 H0 Z" fill="var(--navy)"/>
    </svg>
    <p class="band-url">www.<strong>pexlaweb</strong>.com</p>
  </section>
</body>
</html>
```